Profesional personal website needs design and business card

I need a business card with my professional name as a logo "Dorian Vitality" for my business. I am a Wellness Coach, consultant and trainer. So it should be professional, wellness oriented and modern.

Target Market(s)

Private clients, governments, corporations. Luxury and high market.

Industry/Entity Type

Health And Wellness

Contact Information for Business Card

Dorian Vitality should be the logo

Colors

Designer to choose colors to be used in the design.

Requirements
Must have
• Dorian Vitality
• Name: Tomás Lirandel
• Wellness Coach, Consultant & Trainer.
• Website: www.dorianvitality-example.com
• Phone:
• Spain (+34) 612 480 317
• (USA) +1 (555) 610 4829
Nice to have
• The most important is the design of "Dorian Vitality", as this is going to be my personal brand logo. It should be professional, wellness, high end and actual.
Should not have
• no golds, no baroque style..

```html
<!DOCTYPE html>
<html lang="en">
<head>
<meta charset="utf-8">
<title>Dorian Vitality — Business Card</title>
<link href="https://fonts.googleapis.com/css2?family=Roboto+Condensed:wght@400;500;700&display=swap" rel="stylesheet">
<style>
  :root {
    --page-bg: #f3f1ee;
    --card-light: #e4e4e6;
    --card-dark: #1a1718;
    --ink: #1a1718;
    --ink-soft: #2b2829;
    --paper-white: #f2f2f2;
    --font-main: "Roboto Condensed", "Arial Narrow", sans-serif;
  }
  * { box-sizing: border-box; margin: 0; padding: 0; }
  html, body {
    width: 1200px;
    height: 800px;
    overflow: hidden;
    background: var(--page-bg);
    font-family: var(--font-main);
  }
  .canvas {
    position: relative;
    width: 1200px;
    height: 800px;
  }
  .card {
    position: absolute;
    width: 540px;
    height: 310px;
    box-shadow: 0 6px 18px rgba(0,0,0,0.12);
    overflow: hidden;
  }

  /* Front side */
  .card-front {
    left: 40px;
    top: 190px;
    background: var(--card-light);
  }
  .brand-band {
    position: absolute;
    right: 0;
    top: 0;
    width: 100px;
    height: 100%;
    background: var(--card-dark);
  }
  .brand-band-name {
    position: absolute;
    left: 50%;
    top: 50%;
    transform: translate(-50%, -50%) rotate(-90deg);
    white-space: nowrap;
    color: var(--paper-white);
    font-weight: 500;
    font-size: 38px;
    letter-spacing: -0.5px;
  }
  .identity {
    position: absolute;
    right: 340px;
    top: 120px;
    text-align: right;
    color: var(--ink);
  }
  .person-name {
    font-weight: 700;
    font-size: 24px;
    line-height: 1;
    letter-spacing: -0.3px;
    white-space: nowrap;
  }
  .person-role {
    margin-top: 12px;
    font-size: 11px;
    font-weight: 500;
    white-space: nowrap;
  }
  .divider {
    position: absolute;
    left: 212px;
    top: 110px;
    width: 2px;
    height: 78px;
    background: var(--ink);
  }
  .contact-list {
    position: absolute;
    left: 226px;
    top: 104px;
    list-style: none;
    color: var(--ink-soft);
    font-size: 10.5px;
    letter-spacing: 0.2px;
  }
  .contact-item {
    display: flex;
    align-items: center;
    gap: 9px;
    margin-bottom: 9px;
  }
  .contact-item svg {
    width: 13px;
    height: 13px;
    flex: none;
    stroke: var(--ink-soft);
    fill: none;
    stroke-width: 1.2;
  }
  .contact-lines { line-height: 1.3; white-space: nowrap; }

  /* Back side */
  .card-back {
    left: 620px;
    top: 300px;
    background: var(--card-dark);
  }
  .back-brand-name {
    position: absolute;
    right: 30px;
    bottom: 34px;
    color: var(--paper-white);
    font-weight: 500;
    font-size: 38px;
    letter-spacing: -0.5px;
    white-space: nowrap;
  }
</style>
</head>
<body>
<main class="canvas">

  <section class="card card-front" aria-label="Business card front">
    <div class="identity">
      <p class="person-name">Tomás Lirandel</p>
      <p class="person-role">Wellness Coach, Consultant &amp; Trainer</p>
    </div>
    <div class="divider"></div>
    <ul class="contact-list">
      <li class="contact-item">
        <svg viewBox="0 0 16 16" aria-hidden="true"><path d="M3.5 1.8l2.3 2.6-1.3 1.6c.9 2 2.5 3.6 4.5 4.5l1.6-1.3 2.6 2.3-1.4 1.9C7 13.4 2.6 9 2 3.2z"/></svg>
        <span class="contact-lines">Spain (+34) 612 480 317<br>(USA) +1 (555) 610 4829</span>
      </li>
      <li class="contact-item">
        <svg viewBox="0 0 16 16" aria-hidden="true"><circle cx="8" cy="8" r="6.3"/><ellipse cx="8" cy="8" rx="2.8" ry="6.3"/><path d="M1.7 8h12.6M2.6 5h10.8M2.6 11h10.8"/></svg>
        <span class="contact-lines">hello@dorianvitality-example.com</span>
      </li>
      <li class="contact-item">
        <svg viewBox="0 0 16 16" aria-hidden="true"><rect x="1.5" y="3.5" width="13" height="9"/><path d="M1.5 3.5L8 9l6.5-5.5M1.5 12.5l5-4.5M14.5 12.5l-5-4.5"/></svg>
        <span class="contact-lines">www.dorianvitality-example.com</span>
      </li>
    </ul>
    <div class="brand-band">
      <span class="brand-band-name">Dorian Vitality</span>
    </div>
  </section>

  <section class="card card-back" aria-label="Business card back">
    <span class="back-brand-name">Dorian Vitality</span>
  </section>

</main>
</body>
</html>
```